life insurance quote website design for lepontdoriole.ca

the web site lepontdoriole.ca need a design. we dont like the actuel one but we are open at all new suggestion. visit us at lepontdoriole.ca and you will understand. the principal concurant is tarifsgarantisnord.ca, calculeo.ca, coutprotecfam.ca. We are a life insurance quote site. we found best price available in the canadien industrie. We absolutly want a design with our form in the front page on the top right side like our concurance, we use wordpress at this time. we want to be able to switch language. and to have a logic form. we want to be able to change the color for each type of insurance quote page.we also need a blog in it to post news. and the site will be SEO accurate.

Target Market(s)

Get client fill the quote form

Industry/Entity Type

Insurance

Number of Pages Required

3 page

Font styles to use
Sans Serif

Requirements
Must have
• logic form on the top right first page
• page template for product info stuff, contact, and who we are, blog
• French site
• custum color
Nice to have
• Wordpress design will be appréciate
• switch language english/french

```html
<!DOCTYPE html>
<html lang="fr">
<head>
<meta charset="utf-8">
<title>Le Pont Doriole – Soumission assurance vie</title>
<link rel="stylesheet" href="https://fonts.googleapis.com/css2?family=Open+Sans:wght@400;600;700;800&display=swap">
<style>
:root{
  --navy:#0a3a74;
  --navy-deep:#062c5c;
  --navy-footer:#0b3a72;
  --red:#d9120f;
  --red-dark:#b80c0a;
  --white:#ffffff;
  --text:#4a4a4a;
  --muted:#7d93b6;
  --grey-band:#e6e6e6;
  --field-border:#cfcfcf;
}
*{box-sizing:border-box;margin:0;padding:0}
html,body{width:1200px;height:2473px;overflow:hidden}
body{font-family:"Open Sans",Arial,sans-serif;color:var(--text);background:var(--white);position:relative}
.wrap{width:1002px;margin:0 auto;position:relative}

/* HERO */
.hero{position:relative;height:635px;overflow:hidden}
.hero-photo{position:absolute;inset:0;background:linear-gradient(180deg,#bcd6ec 0%,#d8e6f0 22%,#9fb9c8 38%,#c7c1b2 55%,#cdb79a 75%,#c2a582 100%)}
.brand{position:absolute;left:40px;top:88px;display:flex;align-items:center;gap:10px;font-weight:800;font-size:24px;color:var(--red);letter-spacing:.5px}
.brand-mark{width:18px;height:18px;background:var(--red);border-radius:50%}
.topbar{position:absolute;right:48px;top:20px;display:flex;align-items:center;gap:26px;font-size:12.5px;color:#333}
.topbar span{display:flex;align-items:center;gap:6px}
.login{background:var(--red);color:#fff;padding:5px 12px;border-radius:2px;font-size:12px}
.nav{position:absolute;right:48px;top:64px;display:flex;gap:0;font-size:15px;color:#1f2d44}
.nav a{color:inherit;text-decoration:none;margin-left:62px}
.hero-title{position:absolute;left:82px;top:478px}
.hero-title .l1{font-size:50px;font-weight:800;color:var(--red);line-height:1}
.hero-title .l2{font-size:33px;font-weight:700;color:var(--navy);line-height:1.2;margin-top:2px}
.dots{position:absolute;left:574px;top:599px;display:flex;gap:7px}
.dots i{width:8px;height:8px;border-radius:50%;background:#a9a9a9}
.dots i:first-child{background:var(--red)}

.quote-form{position:absolute;left:709px;top:135px;width:402px;height:500px;background:#fff;box-shadow:0 0 8px rgba(0,0,0,.15)}
.quote-form h2{background:var(--navy);color:#fff;font-size:21px;font-weight:700;text-align:center;height:50px;line-height:50px;letter-spacing:.3px}
.qf-body{padding:18px 24px 0}
.qf-label{font-size:11.5px;color:#333;font-weight:600;margin-bottom:10px}
.req{color:var(--red)}
.field{height:34px;border:1px solid var(--field-border);border-radius:3px;font-size:11.5px;color:#555;padding:0 10px;display:flex;align-items:center;justify-content:space-between;margin-bottom:11px;background:#fff}
.row{display:flex;gap:11px}
.row .field{flex:1}
.sex{flex:1;display:flex;align-items:center;gap:8px;font-size:11.5px;color:#444}
.radio{width:11px;height:11px;border:1px solid #aaa;border-radius:50%;display:inline-block;vertical-align:middle;margin-right:4px}
.check{font-size:11.5px;color:#333;margin:12px 0 0}
.captcha{display:flex;gap:14px;margin-top:14px;align-items:center}
.captcha-img{width:92px;height:34px;background:linear-gradient(90deg,#eee,#ddd)}
.captcha .field{width:170px;margin:0}
.send{display:block;margin-top:16px;height:46px;background:linear-gradient(180deg,#f0201c,var(--red-dark));color:#fff;font-weight:700;font-size:16px;text-align:center;line-height:46px;border-radius:2px}

/* SERVICES */
.services{background:var(--navy);height:475px;color:#fff;text-align:center;padding-top:60px}
.services h2{font-size:30px;font-weight:700}
.services .lead{font-size:13.5px;margin-top:20px}
.svc-grid{display:flex;justify-content:space-between;width:1002px;margin:48px auto 0}
.svc{width:220px}
.svc-icon{width:90px;height:90px;border:2px solid #fff;border-radius:50%;margin:0 auto;display:flex;align-items:center;justify-content:center}
.svc h3{font-size:14.5px;font-weight:600;margin-top:22px}
.svc p{font-size:11.5px;color:var(--muted);line-height:21.5px;margin-top:10px}

/* ABOUT */
.about{display:flex;gap:64px;padding-top:65px}
.about-photo{width:376px;height:250px;background:linear-gradient(135deg,#e8ecef,#c9d2da 55%,#aab4bf)}
.about-text{flex:1;padding-top:8px}
.about-text h2{font-size:24px;color:var(--navy);font-weight:700}
.about-text p{font-size:12.2px;line-height:24px;margin-top:14px;color:#555}
.btn-red{display:inline-block;margin-top:22px;background:var(--red);color:#fff;font-size:13px;font-weight:600;width:143px;height:41px;line-height:41px;text-align:center;border-radius:2px}

/* POSTS */
.posts h2{text-align:center;font-size:23px;color:var(--navy);font-weight:700;margin-top:50px}
.post-grid{display:flex;justify-content:space-between;margin-top:30px}
.post{width:230px}
.post-img{height:161px}
.post h3{font-size:14px;color:var(--navy);font-weight:600;line-height:23px;margin-top:10px}
.post time{display:block;font-size:11.5px;color:#666;margin-top:6px}

/* TESTIMONIALS */
.testimonials{position:absolute;left:0;top:1826px;width:1200px;height:338px;background:var(--grey-band)}
.testimonials h2{text-align:center;font-size:23px;color:var(--navy);font-weight:700;margin-top:44px}
.t-grid{display:flex;justify-content:space-between;margin-top:34px}
.t-item{width:290px;position:relative}
.t-item blockquote{font-size:12.5px;line-height:24px;color:#555;padding:0 24px 0 24px;position:relative}
.t-item blockquote::before{content:"\201C";position:absolute;left:-2px;top:-10px;font-size:34px;color:#c4c4c4;font-family:Georgia,serif}
.t-item blockquote::after{content:"\201D";position:absolute;right:0;bottom:-18px;font-size:34px;color:#c4c4c4;font-family:Georgia,serif}
.t-author{display:flex;align-items:center;gap:14px;margin-top:24px}
.t-avatar{width:50px;height:50px;border-radius:50%;background:linear-gradient(135deg,#b7a898,#7d6e60)}
.t-name{font-size:11.5px;font-weight:700;color:var(--red)}
.t-role{font-size:11.5px;color:#555;margin-top:4px}

/* FOOTER */
.footer{position:absolute;left:0;top:2164px;width:1200px;height:247px;background:var(--navy-footer);color:#fff}
.f-grid{position:relative;height:247px}
.f-col{position:absolute;top:48px}
.f-col h4{font-size:13px;font-weight:700;letter-spacing:.3px}
.f-col p,.f-col li{font-size:11.5px;line-height:23px;list-style:none}
.f-col ul,.f-col p{margin-top:10px}
.f-col .more{font-size:11.5px;font-weight:600;margin-top:8px;display:flex;align-items:center;gap:6px}
.contact-line{display:flex;align-items:center;gap:10px}
.bottombar{position:absolute;left:0;top:2411px;width:1200px;height:62px;background:var(--navy-deep);color:#fff;font-size:11.5px}
.bottombar .wrap{display:flex;justify-content:space-between;align-items:center;height:62px}
.social{display:flex;align-items:center;gap:18px}
.social i{width:10px;height:10px;border-radius:50%;background:#fff;display:inline-block}
</style>
</head>
<body>

<header class="hero">
  <div class="hero-photo" role="img" aria-label="Photo d'une famille courant sur une plage au bord de la mer"></div>
  <div class="brand"><span class="brand-mark"></span>LEPONTDORIOLE.CA</div>
  <div class="topbar">
    <span>English ⌄</span>
    <span><svg width="12" height="12" viewBox="0 0 24 24"><path fill="#d9120f" d="M6.6 10.8a15 15 0 0 0 6.6 6.6l2.2-2.2a1 1 0 0 1 1-.25 11.4 11.4 0 0 0 3.6.57 1 1 0 0 1 1 1V20a1 1 0 0 1-1 1A17 17 0 0 1 3 4a1 1 0 0 1 1-1h3.5a1 1 0 0 1 1 1c0 1.25.2 2.45.57 3.57a1 1 0 0 1-.25 1z"/></svg>1-855-555-0142</span>
    <span><svg width="13" height="10" viewBox="0 0 26 20"><rect width="26" height="20" rx="2" fill="#d9120f"/><path d="M1 2l12 9 12-9" stroke="#fff" stroke-width="2" fill="none"/></svg>contact@lepontdoriole.ca</span>
    <span class="login">Login ⌄</span>
  </div>
  <nav class="nav">
    <a>Accueil</a><a>Produits ⌄</a><a>Soumission ⌄</a><a>Qui Sommes-Nous?</a><a>Nous Joindre</a>
  </nav>
  <div class="hero-title">
    <div class="l1">We are a life</div>
    <div class="l2">insurance quote company</div>
  </div>
  <div class="dots"><i></i><i></i><i></i><i></i></div>

  <form class="quote-form">
    <h2>DEMANDE DE SOUMISSION</h2>
    <div class="qf-body">
      <div class="qf-label">Types of insurance <span class="req">*</span></div>
      <div class="field">- Select - <span>⌄</span></div>
      <div class="row"><div class="field"><span>First name<span class="req">*</span></span></div><div class="field"><span>Last name<span class="req">*</span></span></div></div>
      <div class="field"><span>City<span class="req">*</span></span><span>⌄</span></div>
      <div class="row"><div class="field"><span>Email<span class="req">*</span></span></div><div class="field"><span>Phone<span class="req">*</span></span></div></div>
      <div class="row"><div class="field"><span>Age<span class="req">*</span></span></div><div class="sex">Sex<span class="req">*</span> <span><i class="radio"></i>Male</span> <span><i class="radio"></i>Female</span></div></div>
      <div class="check"><i class="radio"></i> Add a co-applicant</div>
      <div class="check"><i class="radio"></i> I Have Read And Accept The Use And Privacy Policy Of **</div>
      <div class="captcha"><div class="captcha-img" role="img" aria-label="Image de code captcha"></div><div class="field">Type Captcha</div></div>
      <span class="send">ENVOYER</span>
    </div>
  </form>
</header>

<section class="services">
  <h2>What we do?</h2>
  <p class="lead">Simply fill in the insurance quote online form above, clicking on the insurance category that fits your needs.</p>
  <div class="svc-grid">
    <div class="svc">
      <div class="svc-icon"><svg width="44" height="44" viewBox="0 0 44 44" fill="none" stroke="#fff" stroke-width="2"><path d="M6 20a16 16 0 0 1 32 0z" fill="#fff"/><path d="M22 20v16a3 3 0 0 1-6 0"/></svg></div>
      <h3>Assurance Vie</h3>
      <p>Remplissez le formulaire de soumission assurance vie et vous appréciez votre expérience avec nous</p>
    </div>
    <div class="svc">
      <div class="svc-icon"><svg width="44" height="44" viewBox="0 0 44 44" fill="none" stroke="#fff" stroke-width="2"><circle cx="22" cy="18" r="13"/><path d="M22 10v8l6 4"/><rect x="12" y="33" width="20" height="4" rx="2" fill="#fff"/></svg></div>
      <h3>Salaire</h3>
      <p>Remplissez le formulaire de soumission assurance vie et vous appréciez votre expérience avec nous</p>
    </div>
    <div class="svc">
      <div class="svc-icon"><svg width="44" height="44" viewBox="0 0 44 44" fill="none" stroke="#fff" stroke-width="2.5"><circle cx="26" cy="17" r="10"/><path d="M19 24L8 36"/></svg></div>
      <h3>Hypothécaire</h3>
      <p>Remplissez le formulaire de soumission assurance vie et vous appréciez votre expérience avec nous</p>
    </div>
    <div class="svc">
      <div class="svc-icon"><svg width="44" height="44" viewBox="0 0 44 44" fill="none" stroke="#fff" stroke-width="2"><rect x="6" y="8" width="32" height="22" rx="1"/><path d="M22 30v6M15 37h14"/><path d="M13 26v-5M19 26v-8M25 26v-6M31 26v-11" stroke-width="3"/></svg></div>
      <h3>Maladies Graves</h3>
      <p>Remplissez le formulaire de soumission assurance vie et vous appréciez votre expérience avec nous</p>
    </div>
  </div>
</section>

<main class="wrap">
  <section class="about">
    <div class="about-photo" role="img" aria-label="Photo d'un couple rencontrant une conseillère en assurance au bureau"></div>
    <div class="about-text">
      <h2>Find the best insurance at the best price!</h2>
      <p>Whether you are looking for life insurance, mortgage insurance or else you certainly want to pay the most advantageous price. Navigating among the many offers in the field of insurance can be a real headache. But thanks to the intervention of Financial Security Advisors of Le Pont Doriole .ca, will save you hours of fruitless search, and in addition, you will find an insurance policy that suits you, at a price that fully meets the constraints on your financial situation, whatever it is.</p>
      <span class="btn-red">Read more info</span>
    </div>
  </section>

  <section class="posts">
    <h2>Recent Posts</h2>
    <div class="post-grid">
      <article class="post"><div class="post-img" role="img" aria-label="Photo de mains tenant des alliances" style="background:linear-gradient(135deg,#e0c0a8,#b88a6c)"></div><h3>El texto de relleno de las imprentas y archivos de texto</h3><time>Posted on 27 March 2016</time></article>
      <article class="post"><div class="post-img" role="img" aria-label="Photo de mains tenant une jeune pousse dans la terre" style="background:radial-gradient(circle at 50% 60%,#6b4a30,#1a1a1a 70%)"></div><h3>El texto de relleno de las imprentas y archivos de texto</h3><time>Posted on 27 March 2016</time></article>
      <article class="post"><div class="post-img" role="img" aria-label="Photo d'un couple de retraités avec un conseiller" style="background:linear-gradient(135deg,#f1ede8,#c9b7a4 60%,#8ea3bd)"></div><h3>El texto de relleno de las imprentas y archivos de texto</h3><time>Posted on 27 March 2016</time></article>
      <article class="post"><div class="post-img" role="img" aria-label="Photo d'une famille souriante avec deux enfants" style="background:linear-gradient(135deg,#f6f3ef,#dcc8b5 55%,#b79a82)"></div><h3>El texto de relleno de las imprentas y archivos de texto</h3><time>Posted on 27 March 2016</time></article>
    </div>
  </section>
</main>

<section class="testimonials">
  <h2>What our client’s say</h2>
  <div class="wrap t-grid">
    <div class="t-item"><blockquote>Lorem Ipsum is simply dummy text of the printing and typesetting industry. Lorem Ipsum has been the industry's standard dummy text ever since...</blockquote><div class="t-author"><div class="t-avatar" role="img" aria-label="Portrait de client"></div><div><div class="t-name">JULIEN MARCEAU</div><div class="t-role">Business man</div></div></div></div>
    <div class="t-item"><blockquote>Lorem Ipsum is simply dummy text of the printing and typesetting industry. Lorem Ipsum has been the industry's standard dummy text ever since...</blockquote><div class="t-author"><div class="t-avatar" role="img" aria-label="Portrait de client"></div><div><div class="t-name">JULIEN MARCEAU</div><div class="t-role">Business man</div></div></div></div>
    <div class="t-item"><blockquote>Lorem Ipsum is simply dummy text of the printing and typesetting industry. Lorem Ipsum has been the industry's standard dummy text ever since...</blockquote><div class="t-author"><div class="t-avatar" role="img" aria-label="Portrait de client"></div><div><div class="t-name">JULIEN MARCEAU</div><div class="t-role">Business man</div></div></div></div>
  </div>
</section>

<footer class="footer">
  <div class="wrap f-grid">
    <div class="f-col" style="left:0;width:340px">
      <h4>WHO WE ARE?</h4>
      <p>Whether you are looking for life insurance, mortgage insurance or else you certainly want to pay the most advantageous price. Navigating among the many offers in the field of insurance can be a real headache...</p>
      <div class="more">Read more info <svg width="11" height="11" viewBox="0 0 12 12"><circle cx="6" cy="6" r="6" fill="#fff"/><path d="M5 3l3 3-3 3" stroke="#0b3a72" stroke-width="1.6" fill="none"/></svg></div>
    </div>
    <div class="f-col" style="left:410px">
      <h4>WELCOME</h4>
      <ul><li>AccueilProduits</li><li>Soumission</li><li>Qui Sommes-Nous?</li><li>Nous Joindre</li></ul>
    </div>
    <div class="f-col" style="left:600px">
      <h4>INFORMATION</h4>
      <ul><li>Terms &amp; Conditions</li><li>Privacy policy</li><li>Disclaimer</li><li>Contact us</li><li>Sitemap</li></ul>
    </div>
    <div class="f-col" style="left:807px">
      <h4>CONTACT INFO</h4>
      <p>48 rue Vernier, Candiac,<br>Qc, J5R 4K1</p>
      <p class="contact-line"><svg width="11" height="11" viewBox="0 0 24 24"><path fill="#fff" d="M6.6 10.8a15 15 0 0 0 6.6 6.6l2.2-2.2a1 1 0 0 1 1-.25 11.4 11.4 0 0 0 3.6.57 1 1 0 0 1 1 1V20a1 1 0 0 1-1 1A17 17 0 0 1 3 4a1 1 0 0 1 1-1h3.5a1 1 0 0 1 1 1c0 1.25.2 2.45.57 3.57a1 1 0 0 1-.25 1z"/></svg>1-855-555-0142</p>
      <p class="contact-line" style="margin-top:2px"><svg width="12" height="9" viewBox="0 0 26 20"><rect width="26" height="20" rx="2" fill="#fff"/><path d="M1 2l12 9 12-9" stroke="#0b3a72" stroke-width="2" fill="none"/></svg>contact@lepontdoriole.ca</p>
    </div>
  </div>
</footer>

<div class="bottombar">
  <div class="wrap">
    <span>© 2016. Lepontdoriole. All rights reserved</span>
    <span class="social">Connct with our social network : <i></i><i></i><i></i><i></i><i></i></span>
  </div>
</div>

</body>
</html>
```